Web Design Project

Psychotherapy and Counselling Practice needs a landing page web design.

My business "Larkfield Advisory" specialises in the treatment of Anxiety and Depression with a holistic approach, endeavouring to unlock the key that holds us to ransom in a life that is imbalanced, frustrating, and ultimately of our own making due to our own perceptions and behaviours.

There is much that impacts us which we cannot change, but we are always in control of how we think, and how we frame our experiences.....learning to challenge those thoughts and behaviours that are destructive and disempowering opens up a world of joyful possibility. Life is about making choices, learn to make wiser and healthier choices.......

Larkfield Advisory has a client base of individual clients but will seek to expand to offer services to the Corporate world by offering an adjunct to employers for established "Wellness Programs".

Larkfield Advisory is a highly professional, ethically bound business, with the needs of the client at the forefront of all we do.

Larkfield Advisory wishes to avoid the usual "jargon driven" psychobabble offered on many counselling web pages. It aims to be stylishly presented, clean in look and with as few "words" as possible and a largely white background (faster loading and more powerful impact of what is stated), those words contained in the webpage should be meaningful, persuasive and have an impact simply at glance. Larkfield does not want , or expect, those prospective clients in need of support , to be reading through volumes of industry driven cliches.

At this point Larkfield is just looking for a high quality landing page. However in time this will likely expand to include other sections such as case studies, video content etc.

Target Market(s)

Those in need of emotional support, suffering mental health issues, and those simply wanting to become self aware supported by a mindful therapist.

Industry/Entity Type

Industry

Requirements
Must have
• The design must incorporate the Larkfield logo and colour schemes found on the attached files.

```html
<!DOCTYPE html>
<html lang="en">
<head>
<meta charset="utf-8">
<title>Larkfield Advisory</title>
<link rel="stylesheet" href="https://fonts.googleapis.com/css2?family=Open+Sans:wght@300;600;700&display=swap">
<style>
  :root {
    --leaf: #8aa61a;
    --leaf-bright: #97b622;
    --stone: #7b7b7b;
    --stone-light: #9a9a9a;
    --band: #707070;
    --paper: #ffffff;
    --panel: #fbfbfb;
  }
  * { box-sizing: border-box; margin: 0; padding: 0; }
  html, body { width: 1200px; height: 891px; overflow: hidden; background: var(--paper); }
  body { font-family: "Open Sans", Arial, sans-serif; position: relative; }

  .site-nav { position: absolute; top: 82px; right: 72px; display: flex; gap: 30px; }
  .site-nav a { color: var(--leaf); font-weight: 700; font-size: 17px; text-decoration: none; letter-spacing: 0.2px; }

  .hero-panel { position: absolute; left: 0; top: 132px; width: 1200px; height: 560px; background: linear-gradient(180deg, var(--panel), var(--paper)); }

  .brand-name { position: absolute; left: 78px; top: 438px; font-size: 86px; font-weight: 300; color: var(--leaf); letter-spacing: 2px; line-height: 1; }

  .quote { position: absolute; left: 714px; top: 176px; }
  .quote-lead { color: var(--leaf); font-weight: 700; font-size: 21px; }
  .quote-body { margin: 14px 0 0 16px; color: var(--stone); font-weight: 700; font-size: 22px; line-height: 36px; }
  .quote-source { margin: 14px 0 0 18px; color: var(--stone-light); font-weight: 700; font-size: 15px; }

  .practice { position: absolute; left: 741px; top: 425px; color: var(--stone-light); }
  .practice-tagline { font-size: 21px; font-weight: 700; }
  .practice-tagline em { font-style: normal; color: var(--leaf); }
  .practitioner-name { margin-top: 36px; font-size: 21px; font-weight: 700; color: var(--stone); }
  .practitioner-quals { margin-top: 4px; font-size: 15px; font-weight: 700; }
  .contact { margin-top: 30px; font-size: 16px; font-weight: 700; line-height: 27px; }

  .swoosh { position: absolute; left: 0; top: 690px; }

  .site-footer { position: absolute; left: 0; top: 812px; width: 1200px; height: 79px; }
  .copyright { position: absolute; left: 83px; top: 38px; font-size: 12px; font-weight: 700; color: var(--stone); }
  .social { position: absolute; left: 432px; top: 24px; display: flex; gap: 11px; }
  .social span { width: 30px; height: 30px; background: var(--leaf); display: block; }
  .web-address { position: absolute; right: 72px; top: 34px; font-size: 16px; font-weight: 700; color: var(--stone); }
  .web-address em { font-style: normal; color: var(--leaf); }
</style>
</head>
<body>
  <nav class="site-nav">
    <a href="#">HOME</a>
    <a href="#">ABOUT US</a>
    <a href="#">CASE STUDIES</a>
    <a href="#">VIDEO CONTENT</a>
  </nav>

  <div class="hero-panel"></div>

  <div class="brand-name">LARKFIELD</div>

  <blockquote class="quote">
    <p class="quote-lead">“Change the law of life.</p>
    <p class="quote-body">And those who look only to the past<br>or present are to miss the future.”</p>
    <p class="quote-source">( J. R. Whitcombe )</p>
  </blockquote>

  <section class="practice">
    <p class="practice-tagline"><em>Advisory</em> is highly Professional</p>
    <p class="practitioner-name">MARA ELLISON</p>
    <p class="practitioner-quals">BA (Psych) BSc (Hons) Psych MBPS</p>
    <p class="contact">Mobile: 0412 118 903<br>E-mail: mara.ellison@larkmail.com</p>
  </section>

  <svg class="swoosh" width="1200" height="122" viewBox="0 0 1200 122" aria-hidden="true">
    <path d="M0,58 C300,72 700,50 1200,34 L1200,122 L0,122 Z" fill="var(--band)"/>
    <path d="M0,16 C250,44 600,40 1085,20 C650,36 300,60 0,52 Z" fill="var(--leaf-bright)"/>
  </svg>

  <footer class="site-footer">
    <p class="copyright">@Copyright Larkfield 2013 . Alright reserve</p>
    <div class="social"><span></span><span></span></div>
    <p class="web-address">www.<em>larkfieldadvisory</em>.com.au</p>
  </footer>
</body>
</html>
```